Thoroughbred Racing Partnership needs web design

Glimmer of Laurel Partners is a management group who buys horses and races them on both the West and East coasts. The premise of the business is for an investment as little as $500, anyone can be a partner and own a percentage of a horse(s). This is a low cost way of getting involved in the exciting sport of Thoroughbred Racing, without shouldering the heavy financial responsibility. Our target market is mostly males 40+ but we want to include all target markets. We are looking for something very clean and professional, we want to give an image of success. Nothing overly "artsy." I have included the logo in which you can incorporate in the site. Also, the logo colors will be the colors of our "silks." The silks are what the jockey wears and will be an important marketing tool for GOL. We would like a very prominent picture of a racehorse somewhere on the homepage, we want to make it clear that is a website for Horseracing partnerships.

On the top of the site, it should say "Glimmer of Laurel" (on the top)
and below that "Thoroughbred Racing Partnerships." (below that)

The main sections, which should be across the top are:

Home
About Us
Ownership
Stable Roster
News
Contact us

Some of these will have drop down menus.

An example of a competitor website that we like is: www.harrowgatefarm.example
An example of a competitor website that we don't like is: www.paddockvue.example
Updates

Project Deadline Extended
Reason: We have a Board of Directors meeting on the 22nd and we will be making a decision on that day. I'm giving an extension so that all designers are able to submit their designs by the 22nd. Thank you!

Target Market(s)

40+ males

Industry/Entity Type

Business

Requirements
Must have
• our logo must be on the site. We would like at least one bold image of a thoroughbred horse in action. The picture is going to tell the story so it needs to be very eye-catching.

Our slogan should also be included on the website, "Experience the thrill of owning a Racehorse."
Should not have
• cartoons, artsy pictures, pictures of Steeplechase horses or "jumpers." This partnership is for racehorses only, there is not jumping involved with the horses.

```html
<!DOCTYPE html>
<html lang="en">
<head>
<meta charset="utf-8">
<title>Glimmer of Laurel Partners — Thoroughbred Racing Partnerships</title>
<link href="https://fonts.googleapis.com/css2?family=PT+Sans+Narrow:wght@400;700&family=Open+Sans:wght@400;700&family=Arimo:wght@400;700&display=swap" rel="stylesheet">
<style>
:root{
  --navy:#1d3a63;
  --accent:#7fa7c4;
  --accent-strong:#5f93b5;
  --dark:#151515;
  --panel:#252525;
  --footer:#0d3d74;
  --footer-line:#4f7fa6;
  --text-soft:#bdbdbd;
  --white:#ffffff;
}
*{box-sizing:border-box;margin:0;padding:0}
html,body{width:1034px;height:1200px;overflow:hidden;background:var(--dark)}
.page{width:1280px;height:1485px;transform:scale(.8078);transform-origin:0 0;position:relative;font-family:"Arimo",Arial,sans-serif;color:var(--white)}
.abs{position:absolute}

/* hero */
.hero{left:0;top:0;width:1280px;height:688px;overflow:hidden;
  background:linear-gradient(180deg,#3f78b8 0%,#6d9cce 30%,#a9c6e3 60%,#cfe0f0 100%)}
.hero-photo{left:470px;top:125px;width:760px;height:563px;
  background:radial-gradient(ellipse at 55% 60%,rgba(150,80,35,.85) 0%,rgba(130,70,30,.55) 35%,rgba(130,70,30,0) 70%)}
.brand-box{left:150px;top:21px;width:195px;height:104px;background:var(--white);display:flex;align-items:center;justify-content:center;gap:8px;box-shadow:0 2px 6px rgba(0,0,0,.3)}
.brand-box .dot{width:14px;height:14px;border-radius:50%;background:var(--navy)}
.brand-box span{font-family:"PT Sans Narrow",sans-serif;font-weight:700;font-size:30px;color:var(--navy)}
.tagline{right:152px;top:14px;text-align:right;font-family:"Open Sans",sans-serif;font-weight:700;font-size:14px;line-height:25px;color:#eef3f8;text-shadow:0 1px 2px rgba(0,0,0,.4)}
.main-nav{left:345px;top:75px;width:784px;height:50px;background:linear-gradient(#2b2b2b,#0b0b0b);border-radius:0 6px 6px 0;display:flex;justify-content:flex-end}
.main-nav a{font-family:"Open Sans",sans-serif;font-weight:700;font-size:13px;color:var(--white);text-decoration:none;display:flex;align-items:center;padding:0 22px;border-left:1px solid #333}
.main-nav a.active{background:linear-gradient(#7aaacb,#5a8cae);border-left:none}
.slogan{left:152px;top:518px;font-family:"PT Sans Narrow",sans-serif;font-weight:700;font-size:46px;line-height:45px;color:var(--navy)}
.arrow{top:355px}
.dots{left:1029px;top:645px;display:flex;gap:11px}
.dots i{width:16px;height:16px;border-radius:50%;background:#f4f4f4;box-shadow:0 1px 2px rgba(0,0,0,.3)}
.dots i.on{background:var(--accent-strong);border:2px solid #fff}

/* welcome */
.divider-band{left:0;top:688px;width:1280px;height:6px;background:#3a3a3a}
.welcome{left:0;top:694px;width:1280px;height:284px;background:linear-gradient(90deg,#1c1c1c,#111 60%,#161616)}
.welcome-title{left:151px;top:733px;font-family:"PT Sans Narrow",sans-serif;font-size:24px;color:var(--accent)}
.welcome-title b{color:var(--white);font-size:30px;margin-left:6px}
.rule{height:1px;background:#3b3b3b}
.lead{left:152px;top:790px;font-weight:700;font-size:13px}
.body-copy{left:152px;top:816px;width:578px;font-size:12.5px;line-height:19.6px;color:var(--text-soft);letter-spacing:.2px}
.more{font-style:italic;font-size:12.5px;color:var(--accent)}
.video{left:759px;top:728px;width:371px;height:225px;border:1px solid #444;background:linear-gradient(180deg,#d5d9dd,#a9b0b6);overflow:hidden}
.video-name{left:0;right:0;top:110px;text-align:center;font-family:"PT Sans Narrow",sans-serif;font-weight:700;font-size:30px;color:var(--navy);letter-spacing:3px}
.play{left:159px;top:75px}
.controls{left:0;bottom:0;width:100%;height:35px;background:linear-gradient(#2a2a2a,#111)}
.controls .track{left:0;top:0;width:100%;height:6px;background:#555}
.controls .buffer{left:0;top:0;width:122px;height:6px;background:#888}
.controls .played{left:0;top:0;width:30px;height:6px;background:#d21b1b}
.controls .time{left:90px;top:14px;font-size:10px;color:#fff}

/* columns */
.cols{left:0;top:978px;width:1280px;height:300px;background:var(--panel)}
.col-head{font-family:"PT Sans Narrow",sans-serif;font-weight:700;font-size:23px;color:var(--white)}
.col-head em{font-style:normal;font-weight:400;color:var(--accent)}
.sep{top:995px;width:2px;height:270px;background:#1a1a1a;border-right:1px solid #303030}
.col-text{font-size:12.5px;line-height:17px;color:#c8c8c8}
.bullets{list-style:none;font-size:12px;font-weight:700;line-height:20px}
.bullets li::before{content:"»";color:#888;margin-right:10px;font-weight:400}
.bullets li.hl{color:var(--accent)}
.news-item{left:491px;width:297px;height:70px;border-bottom:1px solid #363636}
.date{left:0;top:2px;width:42px;height:42px;background:linear-gradient(#d7d7d7,#9d9d9d);border-radius:4px;text-align:center;color:#333;font-weight:700;font-size:20px;line-height:20px;padding-top:3px}
.date small{display:block;font-size:11px;line-height:12px}
.news-item p{left:63px;top:0;width:234px}
.portrait{left:837px;top:1043px;width:80px;height:80px;background:linear-gradient(#dfe6ee,#8b98a8)}
.quote{left:937px;top:1038px;width:190px;font-size:12.5px;line-height:19.5px;color:#c8c8c8}
.quote b{color:#bbb;font-size:18px;font-family:Georgia,serif}
.author{left:936px;top:1134px;font-weight:700;font-size:13.5px;line-height:21px;color:var(--accent)}
.author span{color:var(--white)}

/* footer */
.footer-line{left:0;top:1278px;width:1280px;height:4px;background:var(--footer-line)}
.footer{left:0;top:1282px;width:1280px;height:203px;background:linear-gradient(#0f4683,#0b3a6e)}
.f-head{font-family:"Open Sans",sans-serif;font-weight:700;font-size:15px;color:var(--white)}
.f-rule{height:1px;background:#2f5f93}
.f-sep{top:1305px;width:1px;height:150px;background:#0a2f59;border-right:1px solid #1b528d}
.links{list-style:none;font-size:12px;line-height:31px}
.links li::before{content:"›";font-weight:700;font-size:17px;margin-right:12px}
.f-text{font-size:12px;line-height:17px}
.email-field{left:455px;top:1395px;width:214px;height:28px;background:#fff;border-radius:2px;color:#777;font-size:12px;line-height:28px;padding-left:8px}
.subscribe{left:586px;top:1433px;width:84px;height:25px;background:linear-gradient(#86b0cf,#4f80a6);border-radius:3px;font-weight:700;font-size:12px;text-align:center;line-height:25px;text-shadow:0 1px 1px rgba(0,0,0,.4)}
.foot-brand{left:965px;top:1318px;width:165px;text-align:center;font-family:"PT Sans Narrow",sans-serif;font-weight:700;font-size:30px;color:#dbe6f1}
.social{left:965px;top:1425px;display:flex;gap:12px}
.social i{width:33px;height:33px;border-radius:50%;background:#9fb2c6}
</style>
</head>
<body>
<div class="page">

  <section class="abs hero" role="img" aria-label="Photograph of a racehorse in full stride under a bright blue sky with clouds">
    <div class="abs hero-photo"></div>
  </section>

  <div class="abs brand-box"><i class="dot"></i><span>GOL Partners</span></div>
  <div class="abs tagline">GLIMMER OF LAUREL<br>THOROUGHBRED RACING PARTNERSHIPS</div>

  <nav class="abs main-nav">
    <a class="active" href="#">HOME</a>
    <a href="#">ABOUT US</a>
    <a href="#">OWNERSHIP</a>
    <a href="#">STABLE ROSTER</a>
    <a href="#">NEWS</a>
    <a href="#">CONTACT US</a>
  </nav>

  <h1 class="abs slogan">Experience the thrill<br>of owning a Racehorse.</h1>

  <svg class="abs arrow" style="left:148px" width="20" height="36" viewBox="0 0 20 36"><path d="M17 2 3 18l14 16" fill="none" stroke="rgba(255,255,255,.35)" stroke-width="2"/></svg>
  <svg class="abs arrow" style="left:1112px" width="20" height="36" viewBox="0 0 20 36"><path d="M3 2l14 16L3 34" fill="none" stroke="rgba(255,255,255,.5)" stroke-width="2"/></svg>
  <div class="abs dots"><i class="on"></i><i></i><i></i><i></i></div>

  <div class="abs divider-band"></div>
  <section class="abs welcome"></section>
  <h2 class="abs welcome-title">Welcome to<b>GOL</b></h2>
  <div class="abs rule" style="left:151px;top:780px;width:575px"></div>
  <p class="abs lead">Glimmer of Laurel Partners is a management group who buys horses and races</p>
  <p class="abs body-copy">Glimmer of Laurel Partners is a management group who buys horses and races them on both the West and East coasts. The premise of the business is for an investment as little as $500, anyone can be a partner and own a percentage of a horse(s). This is a low cost way of getting involved in the exciting sport of Thoroughbred Racing, without shouldering the heavy financial responsibility.</p>
  <a class="abs more" style="left:651px;top:935px">Read More »</a>

  <div class="abs video">
    <div class="abs video-name">GOL PARTNERS</div>
    <svg class="abs play" width="52" height="36" viewBox="0 0 52 36"><circle cx="26" cy="18" r="18" fill="#c81d1d"/><path d="M21 10v16l13-8z" fill="#fff"/></svg>
    <div class="abs controls">
      <div class="abs track"></div><div class="abs buffer"></div><div class="abs played"></div>
      <svg class="abs" style="left:20px;top:13px" width="14" height="14"><rect x="1" y="1" width="4" height="12" fill="#ddd"/><rect x="8" y="1" width="4" height="12" fill="#ddd"/></svg>
      <svg class="abs" style="left:58px;top:13px" width="20" height="14"><path d="M1 5h4l5-4v12l-5-4H1z" fill="#ddd"/></svg>
      <span class="abs time">0:07 <span style="color:#999">/ 2:54</span></span>
      <svg class="abs" style="left:346px;top:12px" width="16" height="16"><path d="M1 5V1h4M11 1h4v4M15 11v4h-4M5 15H1v-4" fill="none" stroke="#ddd" stroke-width="1.5"/></svg>
    </div>
  </div>

  <section class="abs cols"></section>
  <div class="abs sep" style="left:467px"></div>
  <div class="abs sep" style="left:807px"></div>

  <h3 class="abs col-head" style="left:152px;top:998px"><em>Shortly</em> About Us</h3>
  <div class="abs rule" style="left:152px;top:1030px;width:296px"></div>
  <p class="abs col-text" style="left:152px;top:1039px;width:298px">Duis autem veli eum iriure dolor in hendrerit in vulputate velit esse molestie consequat, vel illum dolorel feugiatmul nulla facilisis at vero eros et accumsano et iusto odio dignissim qui blandit praesent luptatuli zrilopil delenit augue duis dolore te feugait nullamol facilisi.</p>
  <ul class="abs bullets" style="left:152px;top:1158px">
    <li>Lorem ipsum dolor sit amet, consectetuer</li>
    <li class="hl">Duis autem veli eum iriure dolor in hendrerit</li>
    <li>Blandit praesent luptatuli zrilopil delenit</li>
  </ul>
  <a class="abs more" style="left:360px;top:1244px">Read More »</a>

  <h3 class="abs col-head" style="left:491px;top:998px"><em>Latest</em> News &amp; Events</h3>
  <div class="abs rule" style="left:491px;top:1030px;width:297px"></div>
  <div class="abs news-item" style="top:1040px"><div class="abs date">29<small>OCT</small></div><p class="abs col-text">Lorem ipsum dolor sit amet, consectetu adipiscing elit, sed diam nonummy nibh consecte nonummy nibh.</p></div>
  <div class="abs news-item" style="top:1110px"><div class="abs date">29<small>OCT</small></div><p class="abs col-text">Lorem ipsum dolor sit amet, consectetu adipiscing elit, sed diam nonummy nibh consecte nonummy nibh.</p></div>
  <div class="abs news-item" style="top:1180px;border-bottom:none"><div class="abs date">29<small>OCT</small></div><p class="abs col-text">Lorem ipsum dolor sit amet, consectetu adipiscing elit, sed diam nonummy nibh consecte nonummy nibh.</p></div>
  <a class="abs more" style="left:710px;top:1244px">Read More »</a>

  <h3 class="abs col-head" style="left:832px;top:998px"><em>Client</em> Testimonials</h3>
  <div class="abs rule" style="left:832px;top:1030px;width:295px"></div>
  <div class="abs portrait" role="img" aria-label="Portrait photo of the client giving the testimonial"></div>
  <p class="abs quote"><b>“</b> Ut wisi enim ad mini veniam, quis nostrud exerci tationullamo corper suscipit lobortis nislutalil uip commodoconsequat. <b>”</b></p>
  <p class="abs author">Mr. Lorem ipsum sit amet<br><span>Chief Executive</span></p>
  <a class="abs more" style="left:1050px;top:1244px">Read More »</a>

  <div class="abs footer-line"></div>
  <footer class="abs footer"></footer>
  <div class="abs f-sep" style="left:430px"></div>
  <div class="abs f-sep" style="left:700px"></div>
  <div class="abs f-sep" style="left:942px"></div>

  <h4 class="abs f-head" style="left:152px;top:1309px">QUICK LINKS</h4>
  <div class="abs f-rule" style="left:152px;top:1335px;width:253px"></div>
  <ul class="abs links" style="left:152px;top:1342px"><li>Home</li><li>About Us</li><li>Ownership</li><li>Stable Roster</li></ul>
  <ul class="abs links" style="left:299px;top:1342px"><li>News</li><li>Contact Us</li></ul>

  <h4 class="abs f-head" style="left:457px;top:1309px">NEWSLETTER</h4>
  <div class="abs f-rule" style="left:457px;top:1335px;width:221px"></div>
  <p class="abs f-text" style="left:456px;top:1348px">Subscribe to our newsletter to receive<br>our special offers and more.</p>
  <div class="abs email-field">Enter your Email Address here</div>
  <div class="abs subscribe">SUBSCRIBE</div>

  <h4 class="abs f-head" style="left:725px;top:1309px">CONTACT DETAILS</h4>
  <div class="abs f-rule" style="left:725px;top:1335px;width:190px"></div>
  <svg class="abs" style="left:723px;top:1350px" width="14" height="20" viewBox="0 0 14 20"><path d="M7 0a7 7 0 0 0-7 7c0 5 7 13 7 13s7-8 7-13a7 7 0 0 0-7-7zm0 10a3 3 0 1 1 0-6 3 3 0 0 1 0 6z" fill="#fff"/></svg>
  <p class="abs f-text" style="left:746px;top:1350px">Sed diam nonummy euismod<br>tincidunt ut laor</p>
  <svg class="abs" style="left:723px;top:1403px" width="16" height="16" viewBox="0 0 16 16"><path d="M3 1l3 3-2 2c1 2 4 5 6 6l2-2 3 3-2 2C7 15 1 9 1 3z" fill="#fff"/></svg>
  <p class="abs f-text" style="left:747px;top:1403px">(000)123-4567</p>
  <svg class="abs" style="left:723px;top:1445px" width="16" height="11" viewBox="0 0 16 11"><rect x=".5" y=".5" width="15" height="10" fill="#fff"/><path d="M1 1l7 5 7-5" fill="none" stroke="#0d3d74"/></svg>
  <p class="abs f-text" style="left:748px;top:1441px">info@golpartners.example</p>

  <div class="abs foot-brand">GOL PARTNERS</div>
  <p class="abs f-text" style="left:965px;top:1391px;width:165px;text-align:center">Copyright © 2013 GOL.</p>
  <div class="abs social" aria-label="Social media links"><i></i><i></i><i></i><i></i></div>

</div>
</body>
</html>
```